Non Profit Company Looking For New Website

The website for Fernvale Quillstone Heritage Society should offer the viewer beautiful photos that inspire condifence and joy and tap into our love of horses.

We would like to see a website that displays trust, quality and confidence. Needs to be responsive and mobile friendly for all browsers and coded for both Android & IOS.

READ ATTACHED WEBSITE TEMPLATE FOR COMPLETE DETAILS ON WHAT WE ARE LOOKING FOR.

Looking for recommmendations if we should use WordPress/WooCommerce for site or Wordpress with Shopify Plug in or just Shopify.

Must be both desktop and mobile friendly with fast page load speed. Need the ability to edit ourselves.

Industry/Entity Type

Non Profit

Coding

Coded - Design and coding required

Number of Pages Required

5+ page

Requirements
Must have
• We would like to see a website that displays trust, quality and confidence. Needs to be responsive and mobile friendly for all browsers and coded for both Android & IOS.

Looking for recommendations if we should use WordPress/WooCommerce for site or Wordpress with Shopify Plug in or just Shopify.

Logo Colour:
Pantone 7621 C

READ TEMPLATE THAT IS ATTACHED
Nice to have
• Like look of this website as a sample:
https://www.quellbrimtorva.com/

Another similar non profit organization
https://pellaworthcindle.com/

```html
<!DOCTYPE html>
<html lang="en">
<head>
<meta charset="utf-8">
<title>Fernvale Quillstone Heritage Society</title>
<link href="https://fonts.googleapis.com/css2?family=Montserrat:wght@400;500;600;700&family=Libre+Baskerville:ital@0;1&display=swap" rel="stylesheet">
<style>
:root{
  --red:#c01f2c;
  --red-dark:#a51a25;
  --ink:#2b2b2b;
  --text:#555;
  --grey:#ececec;
  --light:#f2f2f2;
  --white:#fff;
}
*{box-sizing:border-box;margin:0;padding:0}
html,body{width:1200px;height:3931px;overflow:hidden;background:var(--white)}
body{font-family:"Montserrat",sans-serif;color:var(--ink);position:relative}
.abs{position:absolute}
.section{position:absolute;left:0;width:1200px}
.btn{position:absolute;display:flex;align-items:center;justify-content:center;font-weight:700;font-size:14px;border:2px solid var(--red);color:var(--red);border-radius:3px;text-transform:uppercase;letter-spacing:.2px}
.btn--light{border-color:#fff;color:#fff}
.rule{position:absolute;height:3px;background:var(--red)}
.photo{position:absolute}

/* header */
.header{top:0;height:118px;background:#fff}
.topbar{position:absolute;left:575px;top:0;width:625px;height:48px;background:var(--light);border-bottom-left-radius:40px;display:flex;align-items:center;padding-left:60px;gap:20px}
.social-dot{width:16px;height:16px;background:var(--red);border-radius:3px}
.topbar .call{margin-left:42px;font-size:14px;color:var(--red);display:flex;align-items:center;gap:6px}
.topbar .call b{font-weight:700}
.logo-tab{position:absolute;left:112px;top:0;width:192px;height:162px;background:#fff;border-radius:0 0 60px 60px;z-index:3;display:flex;flex-direction:column;align-items:center;justify-content:center;text-align:center;gap:8px}
.logo-name{font-family:"Libre Baskerville",serif;color:var(--red);font-size:17px;line-height:1.25;letter-spacing:.5px}
.logo-mark{width:26px;height:26px;background:var(--red);border-radius:50%}
.nav{position:absolute;top:78px;left:0;width:1200px;font-size:13px;font-weight:600;color:#444}
.nav span{position:absolute}
.nav .active{color:var(--red)}

/* hero */
.hero{top:118px;height:623px}
.hero-banner{position:absolute;left:210px;top:318px;width:765px;height:194px;background:rgba(192,31,44,.92);border-top-left-radius:70px;border-top-right-radius:70px;color:#fff;text-align:center;font-family:"Libre Baskerville",serif;padding-top:26px}
.hero-banner em{display:block;font-size:31px;margin-bottom:6px}
.hero-banner strong{display:block;font-weight:400;font-size:31px;line-height:43px;letter-spacing:.3px}

/* intro */
.intro{top:741px;height:314px;text-align:center}
.intro h1{position:absolute;top:80px;width:100%;font-size:38px;font-weight:600;color:var(--red);letter-spacing:.5px}
.intro p{position:absolute;top:160px;width:100%;font-size:19px;line-height:26px;color:#333}

/* about */
.about{top:1055px;height:600px}
.about h2{position:absolute;left:644px;top:115px;font-size:31px;font-weight:500;line-height:42px;color:var(--ink)}
.about p{position:absolute;left:646px;width:415px;font-size:13px;line-height:21.5px;color:var(--text)}

/* adopt */
.adopt{top:1655px;height:481px}
.adopt h2{position:absolute;left:139px;top:117px;font-size:30px;font-weight:600;color:#fff}
.adopt p{position:absolute;left:139px;top:186px;width:400px;font-size:16px;line-height:28px;color:#fff}

/* horses */
.horses{top:2136px;height:834px}
.horses h2{position:absolute;top:62px;width:100%;text-align:center;font-size:34px;font-weight:500;color:var(--ink)}
.card{position:absolute;width:333px;height:236px}
.card--featured{border:6px solid #fff;box-shadow:0 0 0 1px #ccc,0 2px 8px rgba(0,0,0,.15)}
.card-info{position:absolute;left:0;bottom:0;width:100%;color:#fff;padding:0 14px 8px}
.card-info .name{font-family:"Libre Baskerville",serif;font-style:italic;font-size:23px;padding:0 8px 10px;border-bottom:1px solid rgba(255,255,255,.5);margin-bottom:10px}
.card-info .meta{display:grid;grid-template-columns:1fr 1fr;row-gap:6px;font-size:12px}

/* contact */
.contact{top:2970px;height:557px}
.contact h2{position:absolute;left:116px;top:68px;font-size:31px;font-weight:400;line-height:36px;color:#fff}
.info{position:absolute;left:110px;color:#fff;display:flex;gap:24px;align-items:center}
.info .ring{width:68px;height:68px;border:2px solid #fff;border-radius:50%;display:flex;align-items:center;justify-content:center}
.info h3{font-size:15px;font-weight:700;margin-bottom:6px}
.info p{font-size:13px;line-height:26px}
.field{position:absolute;left:655px;width:428px;height:44px;border:1.5px solid rgba(255,255,255,.85);color:#fff;font-size:13px;font-weight:600;display:flex;align-items:center;padding-left:20px;gap:12px}
.field i{width:12px;height:12px;background:rgba(255,255,255,.75);border-radius:2px;display:block}
.field--area{height:92px;align-items:flex-start;padding-top:14px}

/* footer */
.footer{top:3527px;height:404px}
.footer .divider{position:absolute;top:0;width:1px;height:333px;background:#ccc}
.footer h4{position:absolute;top:82px;font-size:15px;font-weight:700;color:var(--red);padding-left:30px}
.footer h4::before{content:"";position:absolute;left:0;top:0;width:3px;height:22px;background:var(--red)}
.footer ul{position:absolute;list-style:none;font-size:13px;color:#555}
.footer li{height:30px}
.follow li{display:flex;align-items:center;gap:14px;height:35px}
.follow i{width:18px;height:18px;background:var(--red);border-radius:3px;display:block}
.f-contact{position:absolute;left:640px;top:124px;font-size:13px;line-height:21px;color:#555}
.f-contact b{font-weight:600;color:#444}
.copyright{position:absolute;left:0;top:359px;width:100%;text-align:center;font-size:12px;color:#555}
.bottom-line{position:absolute;left:0;top:333px;width:100%;height:1px;background:#ccc}
</style>
</head>
<body>

<header class="section header">
  <div class="logo-tab">
    <div class="logo-name">FERNVALE<br>QUILLSTONE<br>HERITAGE</div>
    <div class="logo-mark"></div>
  </div>
  <div class="topbar">
    <span class="social-dot" aria-label="Stablebook"></span>
    <span class="social-dot" aria-label="Hoofline"></span>
    <span class="social-dot" aria-label="Paddock Net"></span>
    <span class="social-dot" aria-label="Trotcast"></span>
    <span class="call">
      <svg width="16" height="16" viewBox="0 0 24 24"><path fill="#c01f2c" d="M6.6 10.8a15.2 15.2 0 0 0 6.6 6.6l2.2-2.2c.3-.3.7-.4 1-.2 1.1.4 2.3.6 3.6.6.6 0 1 .4 1 1V20c0 .6-.4 1-1 1A17 17 0 0 1 3 4c0-.6.4-1 1-1h3.5c.6 0 1 .4 1 1 0 1.3.2 2.5.6 3.6.1.3 0 .7-.2 1z"/></svg>
      CALL TODAY: <b>(555) 214-3907</b>
    </span>
  </div>
  <nav class="nav">
    <span class="active" style="left:387px">HOME</span>
    <span style="left:500px">ABOUT</span>
    <span style="left:619px">ADOPT</span>
    <span style="left:738px">HORSES</span>
    <span style="left:861px">DONATE</span>
    <span style="left:993px">CONTACT</span>
  </nav>
  <div class="abs" style="left:387px;top:102px;width:42px;height:2px;background:var(--red)"></div>
</header>

<section class="section hero">
  <div class="photo" role="img" aria-label="Chestnut horse with white blaze standing in a green summer pasture by a fence" style="inset:0;background:linear-gradient(180deg,#3e5a1e 0%,#6f8a34 45%,#a9b84e 75%,#6b8a2a 100%)"></div>
  <div class="photo" aria-hidden="true" style="left:360px;top:0;width:320px;height:330px;background:radial-gradient(ellipse at center,#b8652b 0%,rgba(150,80,30,.6) 45%,rgba(0,0,0,0) 72%)"></div>
  <svg class="abs" style="left:40px;top:252px" width="34" height="44" viewBox="0 0 34 44"><path d="M26 4 8 22l18 18" fill="none" stroke="#fff" stroke-width="3"/></svg>
  <svg class="abs" style="left:1126px;top:252px" width="34" height="44" viewBox="0 0 34 44"><path d="M8 4l18 18L8 40" fill="none" stroke="#fff" stroke-width="3"/></svg>
  <div class="hero-banner">
    <em>We support and develop retired</em>
    <strong>THOROUGHBRED RACEHORSES FOR<br>THEIR NEXT CHAPTER IN LIFE</strong>
  </div>
</section>

<section class="section intro">
  <h1>RETIRE. RETRAIN. REHOME.</h1>
  <div class="rule" style="left:552px;top:136px;width:96px"></div>
  <p>Fernvale Quillstone Heritage Society (FQH) is a registered<br>not-for-profit organization in Fernvale.</p>
</section>

<section class="section about">
  <div class="photo" role="img" aria-label="Young woman resting against a dark bay horse in golden evening light" style="left:0;top:0;width:680px;height:600px;background:linear-gradient(100deg,#5a3a1c 0%,#8a6a3a 35%,#b9a25a 60%,#d9c88a 85%)"></div>
  <svg class="abs" style="left:580px;top:0" width="620" height="600" viewBox="0 0 620 600">
    <path d="M20 0 C40 20 24 60 22 80 C60 20 120 0 200 0 L620 0 L620 600 L40 600 C20 420 20 200 20 0Z" fill="#ececec"/>
  </svg>
  <h2>WHAT IS THOROUGHBRED<br>AFTERCARE?</h2>
  <div class="rule" style="left:646px;top:208px;width:70px"></div>
  <p style="top:234px">The health, safety and welfare of our equine athletes does not end at the finish line, and retirement and aftercare are critical to the success of the racing industry.</p>
  <p style="top:313px">Aftercare is the safe placement of racehorses after their careers as racehorse are completed. Some horses might retire to the breeding shed or broodmare bands, while others are retrained for second careers.</p>
  <div class="btn" style="left:646px;top:428px;width:256px;height:54px">Learn more about us</div>
</section>

<section class="section adopt">
  <div class="photo" role="img" aria-label="Woman greeting a dark horse in a sunlit meadow at sunset" style="left:560px;top:0;width:640px;height:481px;background:linear-gradient(120deg,#e0a24a 0%,#c98838 40%,#7a5a2a 70%,#4d3a22 100%)"></div>
  <svg class="abs" style="left:0;top:0" width="640" height="481" viewBox="0 0 640 481">
    <path d="M0 0 H627 C618 120 612 200 540 240 C612 280 618 360 627 481 H0Z" fill="#c01f2c"/>
    <path d="M627 0 C618 120 612 200 540 240 C612 280 618 360 627 481" fill="none" stroke="#fff" stroke-width="3"/>
  </svg>
  <h2>ADOPT A HORSE</h2>
  <p>Fernvale Quillstone Heritage is committed to helping match you with the perfect horse.</p>
  <div class="btn btn--light" style="left:139px;top:268px;width:173px;height:46px">Adopt now</div>
</section>

<section class="section horses">
  <h2>OUR HORSES</h2>
  <div class="rule" style="left:562px;top:110px;width:76px"></div>

  <div class="card" role="img" aria-label="Bay horse trotting through a meadow" style="left:82px;top:159px;background:linear-gradient(180deg,#3f5a3a 0%,#6f7f44 55%,#c7b24a 100%)"></div>
  <div class="card card--featured" style="left:433px;top:153px;width:350px;height:248px;background:linear-gradient(135deg,#2a2a2a 0%,#4a3325 55%,#6b4a34 100%)" role="img" aria-label="Portrait of a bay gelding wearing a halter">
    <div class="card-info">
      <div class="name">Copper Wren</div>
      <div class="meta">
        <span><b>Birth Year:</b> 2018</span><span><b>Color:</b> Bay</span>
        <span><b>Gender:</b> Gelding</span><span><b>Location:</b> Millbrook, KY</span>
      </div>
    </div>
  </div>
  <div class="card" role="img" aria-label="Black horse standing in a field of red poppies" style="left:800px;top:159px;background:linear-gradient(180deg,#7b9bb0 0%,#5d6f5a 40%,#3a3a36 65%,#c2372a 100%)"></div>

  <div class="card" role="img" aria-label="Brown horse in autumn woods" style="left:82px;top:417px;background:linear-gradient(135deg,#b0643a 0%,#7a3f22 50%,#4b2a18 100%)"></div>
  <div class="card" role="img" aria-label="Chestnut horse standing in sunlit grass" style="left:441px;top:417px;background:linear-gradient(160deg,#7d8d3a 0%,#b0703a 50%,#8a4a22 80%,#5b7a2a 100%)"></div>
  <div class="card" role="img" aria-label="Close view of a horse's head in warm light" style="left:800px;top:417px;background:linear-gradient(135deg,#8a7a4a 0%,#5a4030 50%,#3a2a22 100%)"></div>

  <div class="btn" style="left:494px;top:689px;width:221px;height:50px">More ways to give</div>
</section>

<section class="section contact">
  <div class="photo" role="img" aria-label="Dim pasture with horses and a barn in the background" style="left:0;top:0;width:640px;height:557px;background:linear-gradient(180deg,#2c2c2c 0%,#3a3a36 50%,#262624 100%)"></div>
  <svg class="abs" style="left:520px;top:0" width="680" height="557" viewBox="0 0 680 557">
    <path d="M72 0 H680 V557 H72 C72 440 70 340 10 290 C70 250 72 130 72 0Z" fill="#c01f2c"/>
  </svg>
  <h2>DO YOU HAVE<br>ANY QUESTIONS?</h2>
  <div class="abs" style="left:116px;top:148px;width:76px;height:3px;background:#fff"></div>

  <div class="info" style="top:207px">
    <div class="ring"><svg width="30" height="34" viewBox="0 0 24 28"><path d="M12 2a8 8 0 0 0-8 8c0 6 8 15 8 15s8-9 8-15a8 8 0 0 0-8-8z" fill="none" stroke="#fff" stroke-width="1.5"/><circle cx="12" cy="10" r="3" fill="none" stroke="#fff" stroke-width="1.5"/></svg></div>
    <div><h3>LOCATION</h3><p>Brindle Hollow, Fernvale<br>4120 RR 18, PO Box 772</p></div>
  </div>
  <div class="info" style="top:320px">
    <div class="ring"><svg width="30" height="30" viewBox="0 0 24 24"><path d="M6.6 10.8a15.2 15.2 0 0 0 6.6 6.6l2.2-2.2c.3-.3.7-.4 1-.2 1.1.4 2.3.6 3.6.6.6 0 1 .4 1 1V20c0 .6-.4 1-1 1A17 17 0 0 1 3 4c0-.6.4-1 1-1h3.5c.6 0 1 .4 1 1 0 1.3.2 2.5.6 3.6.1.3 0 .7-.2 1z" fill="none" stroke="#fff" stroke-width="1.4"/></svg></div>
    <div><h3>PHONE NUMBER</h3><p>(555) 214-3907</p></div>
  </div>
  <div class="info" style="top:423px">
    <div class="ring"><svg width="32" height="24" viewBox="0 0 32 24"><rect x="4" y="2" width="26" height="20" fill="none" stroke="#fff" stroke-width="1.5"/><path d="M4 2l13 11L30 2" fill="none" stroke="#fff" stroke-width="1.5"/></svg></div>
    <div><h3>EMAIL US</h3><p>hello@fernvalequill.org</p></div>
  </div>

  <div class="field" style="top:103px"><i></i>First Name</div>
  <div class="field" style="top:159px"><i></i>Last Name</div>
  <div class="field" style="top:214px"><i></i>Email address</div>
  <div class="field" style="top:270px"><i></i>Phone</div>
  <div class="field field--area" style="top:326px"><i></i>Leave Messsage</div>
  <div class="btn btn--light" style="left:658px;top:436px;width:204px;height:48px;gap:8px">Submit message
    <svg width="18" height="16" viewBox="0 0 18 16"><path d="M1 8 17 1 13 15 9 10z" fill="#fff"/></svg>
  </div>
</section>

<footer class="section footer">
  <div class="abs" style="left:112px;top:70px;width:250px;text-align:center">
    <div class="logo-name" style="font-size:24px;line-height:32px">FERNVALE<br>QUILLSTONE<br>HERITAGE</div>
    <div class="logo-mark" style="margin:12px auto 0;width:30px;height:30px"></div>
  </div>
  <div class="abs" style="left:176px;top:318px;width:58px;height:2px;background:var(--red)"></div>

  <div class="divider" style="left:377px"></div>
  <div class="divider" style="left:592px"></div>
  <div class="divider" style="left:909px"></div>

  <h4 style="left:394px">NAVIGATION</h4>
  <ul style="left:427px;top:123px">
    <li>About Us</li><li>Adopt</li><li>Horses</li><li>Donate</li><li>Contact Us</li>
  </ul>

  <h4 style="left:608px">CONTACT US</h4>
  <div class="f-contact">
    88 Harlow Lane P.O. Box 40<br>Ashby, Westmark&nbsp; K2R 4T8<br>
    <div style="height:14px"></div>
    <b>Phone Number</b><br>(555) 214-3906<br>
    <div style="height:14px"></div>
    <b>Email address</b><br>hello@fernvalequill.org
  </div>

  <h4 style="left:930px">FOLLOW US</h4>
  <ul class="follow" style="left:958px;top:118px">
    <li><i></i>Stablebook</li><li><i></i>Hoofline</li><li><i></i>Paddock Net</li><li><i></i>Trotcast</li>
  </ul>

  <div class="bottom-line"></div>
  <div class="copyright">©2021 Copyright Fernvale. All Right Reserved</div>
</footer>

</body>
</html>
```